Im want a website LIKE VRX's and FleetHollow.com's with product payment options like Trenzo's

I need a website LIKE VRX with a header made EXACTLY LIKE THAT OF FLEETHOLLOWS .

The front page photo should be like that of FLEETHOLLOW's webpage as well.

The name of the website will be called "M.K. (Caldera Key)".

We will be targeting ALL MARKETS in a small town in central Panama and charging businesses "listing fees" like a phone book does but also providing informational blogs, news, and other interesting activities.

THIS IS A MULTI PAGE WEBSITE

THIS IS WHERE VRX's website meets Brivelle/FleetHollow.

Once the layout is built I will tweak and modify, add information, and upload items for sale.

Here is a list of specific categories that should be listed out above the front page header image/search bar

-- Home -- News -- Travel -- Activities -- Shop & Dine -- Store -- More... --

These categories should be spread across the bottom of the page in three sections:

WHATS SO GREAT ABOUT (Caldera Key),
HAND PICKED TOURS
ACTIVITIES etc.

Also lets use www.Trenzo.example 's
"HOT DESTINATIONS"
"BEAT THE BEST PRICES IN CALDERA"
"OCTOBERS INSIDER PICKS"
"TOP DESTINATIONS"
and spread them in four sections side-by-side near the bottom of the page.

Overall I would like to see the finished product to be something LIKE VRX's and FleetHollows.

WE NEED ONLINE PAYMENT OPTIONS LIKE BRIVELLE'S WEBSITE HAS

This will be a desktop website but should be very mobile friendly as well.

-rodmund

P.S. Good luck!

If it isn't already too late to change the website name, the name of the website should be "Caldera Key". Added Friday, October 9, 2015

What do you guys think the budget should be to win this? Added Saturday, October 10, 2015

www.palmorra.example is the most amazing simple site. Whoever can make me a replica with my specifications will win immediately!!!! Added Sunday, October 18, 2015

OMG www.palmorra.example is the bomb!So simple and elegant. Whoever can make me an EXACT REPLICA OF WWW.PALMORRA.EXAMPLE as my site with the specifications mentioned in my brief will take home the $825.00 immediately! Good luck amigos! Added Sunday, October 18, 2015

Does anybody know how to add recurring monthly billing options on this website? Added Sunday, October 18, 2015

ALL MARKETS

Product

Coded - Design and coding required

5+ page

• Coinvey payment options.
• I must be able to add and remove photos/text and video from the HTML files in the page.
• Be creative my friends, and may the odds be forever in your favor!
• I added some photos of a good layout for our page below.

```html
<!DOCTYPE html>
<html lang="en">
<head>
<meta charset="utf-8">
<title>Caldera Source – Travel</title>
<link href="https://fonts.googleapis.com/css2?family=Roboto:wght@300;400;500;700&family=Lora:ital@1&display=swap" rel="stylesheet">
<style>
:root{
  --orange:#f6a623;
  --dark:#1f1f1f;
  --darker:#121212;
  --nav:#2a2a2a;
  --page:#efefef;
  --white:#ffffff;
  --text:#333333;
  --muted:#777777;
  --line:#cfcfcf;
  --link:#e89a1c;
  --blue:#4aa3df;
}
*{box-sizing:border-box;margin:0;padding:0}
html,body{width:829px;height:1200px;overflow:hidden}
body{font-family:"Roboto",sans-serif;color:var(--text);background:var(--page);position:relative}
.abs{position:absolute}
/* header */
.topbar{left:0;top:0;width:829px;height:24px;background:var(--dark);color:#eee;font-size:8px}
.topbar .contact{left:176px;top:7px;display:flex;gap:14px;align-items:center}
.topbar .contact span{display:flex;align-items:center;gap:6px}
.topbar .auth{right:72px;top:6px;font-weight:500;font-size:8.5px;display:flex;gap:5px;align-items:center}
.topbar .auth .login{color:var(--orange)}
.mainnav{left:0;top:24px;width:829px;height:22px;background:var(--nav)}
.mainnav ul{list-style:none;display:flex;position:absolute;left:164px;top:0;height:22px}
.mainnav li{color:#f0f0f0;font-size:8px;padding:0 12px;line-height:22px}
.mainnav li.active{background:var(--orange);color:#fff}
.cart{left:708px;top:26px;width:52px;height:19px;background:var(--orange);color:#222;font-size:7.5px;font-weight:500;display:flex;align-items:center;justify-content:center;gap:4px}
.subnav{left:0;top:46px;width:829px;height:22px;background:rgba(245,240,228,.95)}
.subnav ul{list-style:none;display:flex;position:absolute;left:164px;top:0}
.subnav li{font-size:7.5px;line-height:22px;padding:0 12px;color:#333}
.subnav li:first-child{background:#e3dccb}
.hero{left:0;top:68px;width:829px;height:106px;background:linear-gradient(90deg,#3a2a1a 0%,#6b4b25 35%,#2b2520 55%,#8a6a30 80%,#b08840 100%)}
.hero h1{position:absolute;left:73px;top:34px;font-weight:400;font-size:28px;color:#fff;letter-spacing:1px}
.logo{left:69px;top:0;width:94px;height:73px;background:var(--orange);display:flex;flex-direction:column;align-items:center;justify-content:flex-end;padding-bottom:8px;gap:10px}
.logo .mark{width:26px;height:26px;background:#fff}
.logo .name{font-size:9px;color:#fff;font-weight:500}
/* main */
.slider{left:69px;top:230px;width:455px;height:420px;background:#fff}
.slider .photo{width:455px;height:278px;background:linear-gradient(180deg,#5d7691 0%,#8ea0ae 35%,#b59774 60%,#8d6b47 100%);position:relative}
.arrow{position:absolute;top:120px}
.slider h2{position:absolute;left:22px;top:295px;font-weight:300;font-size:18.5px;color:#333}
.slider p{position:absolute;left:22px;top:326px;width:410px;font-size:7.5px;line-height:13px;color:#555}
.thumbs{position:absolute;left:20px;top:365px;display:flex;gap:5px;align-items:flex-start}
.thumbs .t{width:34px;height:34px;background:linear-gradient(135deg,#5fb8c9,#d9cfa8)}
.thumbs .t.on{border-bottom:3px solid var(--orange);height:37px}
.thumbs .nav{position:absolute;top:10px}
.bodycopy{left:69px;top:665px;width:460px;font-size:9px;line-height:13px;color:#333}
.sidebar{left:542px;top:230px;width:218px}
.sidebar .head{height:30px;background:var(--orange);color:#fff;font-size:11.5px;font-weight:500;padding:8px 16px}
.sidebar .photo{height:118px;background:linear-gradient(180deg,#8fb6d8 0%,#c4d7e5 45%,#5f6f78 70%,#3d6b3a 100%)}
.sidebar h3{font-weight:300;font-size:18px;line-height:21px;color:#444;margin-top:18px}
.sidelist{list-style:none;margin-top:6px}
.sidelist li{display:flex;align-items:center;gap:12px;height:43px;border-bottom:1px solid var(--line);font-size:9.5px;color:#333}
.sidelist .t{width:42px;height:32px;background:linear-gradient(135deg,#4f8fc7,#e6b15a)}
/* lower */
.lower{left:0;top:757px;width:829px;height:219px;background:#f8f8f8}
.sechead{display:flex;align-items:center;gap:6px;font-size:15.5px;color:#333}
.dest{left:69px;top:20px}
.destgrid{display:grid;grid-template-columns:113px 113px;row-gap:5px;margin-top:14px}
.destgrid .d{display:flex;align-items:center;gap:5px}
.destgrid .t{width:31px;height:31px;background:linear-gradient(135deg,#7a6a9a,#e0a050);flex:none}
.destgrid span{display:block;width:46px;border-bottom:1px solid #999;font-size:7.5px;color:var(--link);padding-bottom:4px}
.pick{left:304px;top:20px}
.pick .photo{margin-top:14px;margin-left:4px;width:217px;height:139px;background:linear-gradient(180deg,#8aa0a5 0%,#4d6b44 50%,#5d5a40 100%);position:relative}
.pick .cap{position:absolute;left:0;bottom:0;width:100%;height:20px;background:rgba(20,20,20,.75);color:#fff;font-size:7.5px;padding:5px 6px}
.pick .pa{position:absolute;top:55px;width:17px;height:27px;background:rgba(0,0,0,.6);color:#fff;font-size:11px;text-align:center;line-height:26px}
.client{left:542px;top:20px}
.quote{position:absolute;left:32px;top:48px;width:218px;height:102px;background:#fff;border:1px solid #e2e2e2;padding:14px 14px;font-family:"Lora",serif;font-style:italic;font-size:8.5px;line-height:14.5px;color:#999}
.dots{position:absolute;left:32px;top:160px;display:flex;gap:3px}
.dots i{width:5px;height:5px;border-radius:50%;background:#ccc}
.dots i.on{background:#999}
.who{position:absolute;left:100px;top:157px;width:132px;text-align:right;font-family:"Lora",serif;font-style:italic;color:#555}
.who b{display:block;font-weight:400;font-size:10.5px;color:#444}
.who small{font-size:8.5px;color:#777}
/* footer */
.footer{left:0;top:976px;width:829px;height:192px;background:var(--dark);color:#aaa}
.fcol{position:absolute;top:0}
.fcol h4{font-size:8px;font-weight:700;color:#fff;margin-top:36px;margin-bottom:10px}
.fabout{left:69px;top:40px;width:160px}
.fabout .mark{width:42px;height:42px;background:#fff;opacity:.9}
.fabout .name{font-size:9px;color:var(--orange);margin-top:8px;font-weight:500}
.fabout p{font-size:7.5px;line-height:13.5px;color:#888;margin-top:2px}
.vline{position:absolute;top:24px;width:1px;height:130px;background:#333}
.social a{display:flex;align-items:center;gap:6px;width:79px;height:17px;margin-bottom:4.5px;color:#fff;font-size:8px;padding-left:7px;text-decoration:none;border-radius:2px}
.social a i{width:6px;height:6px;background:#fff;display:block}
.fb{background:#3b5b9a}.tw{background:#27a9e1}.gp{background:#dc4a38}.pi{background:#cb2027}
.flinks{list-style:none;font-size:7.5px;color:#888}
.flinks li{margin-bottom:11px}
.cols2{display:grid;grid-template-columns:54px 54px;row-gap:11px;font-size:7.5px;color:#888}
.tweet{font-size:7px;line-height:9.5px;color:#ccc;margin-bottom:10px;padding-bottom:4px;border-bottom:1px solid #333;width:120px}
.tweet b{color:#fff}
.tweet a{color:var(--blue);text-decoration:none}
.copy{left:0;top:1168px;width:829px;height:32px;background:var(--darker);color:#fff;font-size:7.5px;font-weight:700;padding:11px 69px}
</style>
</head>
<body>

<header>
  <div class="abs topbar">
    <div class="abs contact">
      <span><svg width="12" height="9" viewBox="0 0 12 9"><rect x=".5" y=".5" width="11" height="8" fill="none" stroke="#fff"/><path d="M.5 .5l5.5 4.5 5.5-4.5" fill="none" stroke="#fff"/></svg>hello@calderasource.example</span>
      <span><svg width="10" height="10" viewBox="0 0 10 10"><path d="M2 0l2 2.5-1 1.5c.8 1.5 1.5 2.2 3 3l1.5-1L10 8 8.5 10C4 9.5.5 6 0 1.5z" fill="#fff"/></svg>1800-555-0142</span>
    </div>
    <div class="abs auth">
      <svg width="11" height="11" viewBox="0 0 11 11"><path d="M4 1h6v9H4M1 5.5h6M5 3.5l2 2-2 2" fill="none" stroke="#fff"/></svg>
      <span class="login">Login</span><span>/</span><span>Sign Up</span>
    </div>
  </div>
  <nav class="abs mainnav">
    <ul>
      <li class="active">Home</li><li>Store</li><li>News</li><li>Activities</li><li>Travel</li><li>Shop &amp; Dine</li><li>More</li><li>Contact</li>
    </ul>
  </nav>
  <div class="abs cart">
    <svg width="13" height="10" viewBox="0 0 13 10"><path d="M0 1h2.5l1.5 6h7l1.5-4.5H3.5" fill="none" stroke="#222" stroke-width="1.2"/><circle cx="5" cy="9" r="1" fill="#222"/><circle cx="10" cy="9" r="1" fill="#222"/></svg>CART
  </div>
  <nav class="abs subnav">
    <ul><li>Home Page 1</li><li>Home Page 2</li><li>Home Page 3</li><li>Home Page 4</li><li>Home Page 5</li></ul>
  </nav>
  <section class="abs hero" role="img" aria-label="Couple driving a vintage convertible through golden fields">
    <h1>Travel</h1>
  </section>
  <div class="abs logo"><span class="mark"></span><span class="name">Caldera Source</span></div>
</header>

<main>
  <article class="abs slider">
    <div class="photo" role="img" aria-label="Hot air balloons over rocky valley landscape">
      <svg class="arrow" style="left:4px" width="30" height="40" viewBox="0 0 30 40"><path d="M24 2L6 20l18 18" fill="none" stroke="#fff" stroke-width="3"/></svg>
      <svg class="arrow" style="right:4px" width="30" height="40" viewBox="0 0 30 40"><path d="M6 2l18 18L6 38" fill="none" stroke="#fff" stroke-width="3"/></svg>
    </div>
    <h2>Lorem ipsum is simply dummy text</h2>
    <p>Contrary to popular belief, Lorem Ipsum is not simply random text. It has roots in a piece of classical Latin literature from 45 BC, making it over 2000 years old.</p>
    <div class="thumbs">
      <svg class="nav" style="left:-12px" width="8" height="14" viewBox="0 0 8 14"><path d="M7 1L1 7l6 6" fill="none" stroke="#999"/></svg>
      <div class="t on" role="img" aria-label="Beach thumbnail"></div><div class="t" role="img" aria-label="Aerial sea thumbnail"></div><div class="t" role="img" aria-label="Beach thumbnail"></div><div class="t" role="img" aria-label="Coast thumbnail"></div><div class="t" role="img" aria-label="Lagoon thumbnail"></div><div class="t" role="img" aria-label="Beach thumbnail"></div><div class="t" role="img" aria-label="Aerial sea thumbnail"></div><div class="t" role="img" aria-label="Beach thumbnail"></div><div class="t" role="img" aria-label="Coast thumbnail"></div><div class="t" role="img" aria-label="Lagoon thumbnail"></div>
      <svg class="nav" style="left:422px" width="8" height="14" viewBox="0 0 8 14"><path d="M1 1l6 6-6 6" fill="none" stroke="#666"/></svg>
    </div>
  </article>
  <p class="abs bodycopy">Contrary to popular belief, Lorem Ipsum is not simply random text. It has roots in a piece of classical Latin literature from 45 BC, making it over 2000 years old.Contrary to popular belief, Lorem Ipsum is not simply random text. It has roots in a piece of classical Latin literature from 45 BC, making it over 2000 years old.Contrary to popular belief, Lorem Ipsum is not simply random text. It has roots in a piece of classical Latin literature from 45 BC, making it over 2000 years old.</p>

  <aside class="abs sidebar">
    <div class="head">More From Travel</div>
    <div class="photo" role="img" aria-label="City skyline above a green park"></div>
    <h3>Lorem ipsum is simply<br>dummy text</h3>
    <ul class="sidelist">
      <li><span class="t" role="img" aria-label="Tower landmark"></span>Lorem Ipsum is simply dummy text</li>
      <li><span class="t" role="img" aria-label="Harbour town"></span>Contrary to popular belief</li>
      <li><span class="t" role="img" aria-label="Sunset with plane"></span>Lorem Ipsum is simply dummy text</li>
      <li><span class="t" role="img" aria-label="Balloon in blue sky"></span>Contrary to popular belief</li>
      <li><span class="t" role="img" aria-label="Traveller at viewpoint"></span>Lorem Ipsum is simply dummy text</li>
    </ul>
  </aside>

  <section class="abs lower">
    <div class="abs dest">
      <div class="sechead"><svg width="14" height="14" viewBox="0 0 14 14"><circle cx="7" cy="7" r="6" fill="none" stroke="#f6a623" stroke-width="1.3"/><path d="M1 7h12M7 1c-3 3-3 9 0 12M7 1c3 3 3 9 0 12" fill="none" stroke="#f6a623"/></svg>Hot Destinations</div>
      <div class="destgrid">
        <div class="d"><i class="t" role="img" aria-label="Paris"></i><span>PARIS</span></div>
        <div class="d"><i class="t" role="img" aria-label="Florence"></i><span>FLORENCE</span></div>
        <div class="d"><i class="t" role="img" aria-label="Las Vegas"></i><span>LAS VEGAS</span></div>
        <div class="d"><i class="t" role="img" aria-label="Venice"></i><span>VENICE</span></div>
        <div class="d"><i class="t" role="img" aria-label="Rome"></i><span>ROME</span></div>
        <div class="d"><i class="t" role="img" aria-label="Milan"></i><span>MILAN</span></div>
        <div class="d"><i class="t" role="img" aria-label="London"></i><span>LONDON</span></div>
        <div class="d"><i class="t" role="img" aria-label="Sydney"></i><span>SYDNEY</span></div>
      </div>
    </div>
    <div class="abs pick">
      <div class="sechead"><svg width="16" height="15" viewBox="0 0 16 15"><path d="M1 1h4v4H1zM11 1h4v4h-4zM3 5v9M13 5v9M3 9h10M6 12h4" fill="none" stroke="#f6a623" stroke-width="1.2"/></svg>October Insider's Pick</div>
      <div class="photo" role="img" aria-label="Mountain ruins with llama in the foreground">
        <span class="pa" style="left:0">«</span><span class="pa" style="right:0">»</span>
        <div class="cap">Machu Picchu Day Trip from Cusco</div>
      </div>
    </div>
    <div class="abs client">
      <div class="sechead"><svg width="14" height="12" viewBox="0 0 14 12"><path d="M7 1C3.5 1 1 3 1 5.5 1 7 2 8 3 8.8L2.5 11 5.5 9.7c.5.1 1 .2 1.5.2 3.5 0 6-2 6-4.4S10.5 1 7 1z" fill="none" stroke="#f6a623" stroke-width="1.2"/></svg>What Client Say</div>
      <div class="quote">Aenean lacinia bibendum nulla sed consectetur. Curabitur blandit tempus porttitor. Amet Fusce Aenean Parturien. Cras justo odio, dapibus ac facilisis in, egestas eget quam.</div>
      <div class="dots"><i></i><i class="on"></i><i></i></div>
      <div class="who"><b>Mira Olen</b><small>Editor of Travel Mag</small></div>
    </div>
  </section>
</main>

<footer class="abs footer">
  <div class="abs fabout">
    <div class="mark"></div>
    <div class="name">Caldera Source</div>
    <p>Lorem Ipsum is simply dummy text of the printing and typesetting industry. Lorem Ipsum has been the industry's standard dummy text ever since the 1500.</p>
  </div>
  <span class="vline" style="left:241px"></span>
  <div class="fcol social" style="left:257px"><h4>FOLLOW US</h4>
    <a class="fb"><i></i>friendnet</a><a class="tw"><i></i>chirper</a><a class="gp"><i></i>circles +</a><a class="pi"><i></i>pinboard</a>
  </div>
  <span class="vline" style="left:357px"></span>
  <div class="fcol" style="left:372px"><h4>BEST TOURS</h4>
    <ul class="flinks"><li>Camping holidays</li><li>Self-catering holidays</li><li>Safaris &amp; wildlife</li><li>Activities &amp; Adventures</li><li>Food &amp; wine holidays</li></ul>
  </div>
  <div class="fcol" style="left:479px"><h4>POPULAR COUNTRIES</h4>
    <div class="cols2"><span>France</span><span>Spain</span><span>Ukraine</span><span>Turkey</span><span>India</span><span>France</span><span>Spain</span><span>Ukraine</span><span>Turkey</span><span>India</span></div>
  </div>
  <span class="vline" style="left:592px"></span>
  <div class="fcol" style="left:606px"><h4>LATEST TWEETS</h4>
    <p class="tweet"><b>TaviPlays</b> RPX 5 <a>https://lnk.example/Tl5XUg</a><br>@taviplays <a>https://lnk.example/Kg5AAn</a></p>
    <p class="tweet"><b>TaviPlays</b> RPX 5 <a>https://lnk.example/Tl5XUg</a><br>@taviplays <a>https://lnk.example/Kg5AAn</a></p>
    <p class="tweet"><b>TaviPlays</b> RPX 5 <a>https://lnk.example/Tl5XUg</a><br>@taviplays <a>https://lnk.example/Kg5AAn</a></p>
  </div>
</footer>
<div class="abs copy">COPYRIGHT @ 2015 CALDERA. ALL RIGHTS RESERVED.</div>

</body>
</html>
```